Construction company that specializes in roofing and siding

https://maplecrestbuild.example/featured-projects/

https://www.bramwickhomesllc.example/#

https://www.tallgrovecontractors.example/residential-siding-services/

Please model a website after these examples
I posted a doc that has some content to get you started. I will upload more content and photos as the site progresses.

Coded - Design and coding required

5+ page

```html
<!DOCTYPE html>
<html lang="en">
<head>
<meta charset="utf-8">
<title>Stonehaven Construction</title>
<link rel="stylesheet" href="https://fonts.googleapis.com/css2?family=Audiowide&family=Montserrat:wght@400;500;600&display=swap">
<style>
:root{
  --black:#000;
  --ink:#0d0d0d;
  --graphite:#3a3a3a;
  --steel:#5e5e5e;
  --ash:#8a8a8a;
  --white:#fff;
  --soft:#d6d6d6;
  --display:"Audiowide",sans-serif;
  --body:"Montserrat",sans-serif;
}
*{box-sizing:border-box;margin:0;padding:0}
html,body{width:1200px;height:4003px;overflow:hidden;background:var(--black);color:var(--white);font-family:var(--body)}
.page{position:relative;width:1200px;height:4003px}
.abs{position:absolute}
.display{font-family:var(--display);text-transform:uppercase;letter-spacing:1px}

/* header */
.topbar{top:0;left:0;width:1200px;height:39px;background:#4a4a4a;font-size:14px}
.topbar .mail{left:104px;top:11px}
.topbar .phone{left:765px;top:11px}
.social{top:8px;display:flex;gap:8px;left:985px}
.social span{width:23px;height:23px;border-radius:50%;background:var(--white);display:block}
.navbar{top:39px;left:0;width:1200px;height:87px;background:var(--black);font-size:16px}
.navbar a{position:absolute;top:34px;color:var(--white);text-decoration:none}
.caret{font-size:11px;margin-left:3px}
.brand{left:500px;top:10px;width:200px;text-align:center}
.brand .mark{width:40px;height:40px;background:var(--steel);margin:0 auto 10px}
.brand .name{font-family:var(--display);font-size:19px;color:var(--soft);letter-spacing:1px}

/* hero */
.hero{top:126px;left:0;width:1200px;height:700px;background:linear-gradient(160deg,#7b7b7b 0%,#5b5b5b 45%,#6a6a6a 100%)}
.hero-copy{top:286px;left:0;width:1200px;text-align:center}
.hero-copy .eyebrow{font-size:23px}
.hero-copy h1{font-size:52px;line-height:52px;margin-top:14px;font-weight:400}
.hero-copy p{font-size:17px;line-height:24px;margin:24px auto 0;width:430px}
.btn{display:inline-block;font-family:var(--display);text-transform:uppercase;color:var(--black);background:linear-gradient(90deg,#f2f2f2,#9a9a9a);border-radius:0 22px 0 22px;font-size:16px;letter-spacing:1px}
.hero .btn{margin-top:26px;padding:11px 26px;background:linear-gradient(90deg,#d9d9d9,#7e7e7e)}
.dots{top:643px;left:571px;display:flex;gap:8px}
.dots span{width:14px;height:14px;border-radius:50%;background:var(--white)}
.dots span:first-child{background:transparent;border:2px solid var(--white)}

/* services */
.services{top:800px;left:0;width:1200px;height:642px;background:linear-gradient(180deg,#3f3f3f,#6a6a6a)}
.section-title{width:1200px;left:0;text-align:center;font-size:44px;font-weight:400}
.card{top:200px;width:308px;height:324px;background:var(--white);border-radius:40px 40px 150px 150px;display:flex;align-items:center;justify-content:center}
.card .photo{width:220px;height:220px;border-radius:50%;display:flex;flex-direction:column;align-items:center;justify-content:center;gap:10px;font-family:var(--display);font-size:20px}
.card .arrow{width:16px;height:16px;border-radius:50%;background:var(--white);color:#333;font-size:11px;text-align:center;line-height:16px;font-family:var(--body)}
.slider-arrow{width:18px;height:18px;border-radius:50%;background:var(--white);color:#333;font-size:12px;line-height:18px;text-align:center;top:344px}

/* about */
.about{top:1442px;left:0;width:1200px;height:636px;background:var(--black)}
.about .frame{left:145px;top:138px;width:368px;height:375px;border:2px solid var(--soft)}
.about .city{left:104px;top:109px;width:368px;height:386px;background:linear-gradient(180deg,#8d7fd0,#3a4a7a 55%,#6a4a3a)}
.about .worker{left:296px;top:325px;width:264px;height:231px;background:linear-gradient(180deg,#e6e6e6,#b88a6a 60%,#6d6d6d)}
.about-copy{left:637px;top:146px;width:430px}
.about-copy h2{font-size:34px;font-weight:400;margin-bottom:14px}
.about-copy p{font-size:15.5px;line-height:25px;margin-bottom:9px}
.about-copy .btn{margin-top:12px;padding:12px 26px;font-size:15px}

/* promise */
.promise{top:2078px;left:0;width:1200px;height:598px;background:linear-gradient(180deg,#2e2e2e,#1f1f1f)}
.avatar{left:548px;top:190px;width:104px;height:104px;border-radius:50%;background:linear-gradient(180deg,#8e8e8e,#5a5a5a);border:4px solid #bdbdbd}
.promise p{left:200px;width:800px;text-align:center;font-size:18.5px;line-height:32px;top:330px}
.promise .sign{top:416px;left:0;width:1200px;text-align:center}
.sign .sincerely{font-size:19px;margin-bottom:6px}
.sign .who{font-family:var(--display);font-size:13px;line-height:24px;letter-spacing:1px}

/* work */
.work{top:2676px;left:0;width:1200px;height:836px;background:var(--black)}
.work .intro{top:152px;left:150px;width:900px;text-align:center;font-size:16.5px;line-height:32px}
.tabs{top:228px;left:0;width:1200px;display:flex;justify-content:center;gap:24px;font-family:var(--display);font-size:12.5px;color:#777;letter-spacing:1px}
.tabs .on{color:var(--white)}
.compare{top:306px;left:180px;width:841px;height:421px;overflow:hidden}
.compare .before{left:0;top:0;width:421px;height:421px;background:linear-gradient(180deg,#bfbfbf 0%,#a8a8a8 35%,#3a3a3a 55%,#e2e2e2 100%)}
.compare .after{left:421px;top:0;width:420px;height:421px;background:linear-gradient(180deg,#7e9ac6 0%,#a9c0de 35%,#2e3548 55%,#e8e8ea 100%)}
.compare .divider{left:419px;top:0;width:3px;height:421px;background:var(--white)}
.compare .handle{left:399px;top:180px;width:44px;height:60px;border:3px solid var(--white);border-radius:24px;background:rgba(0,0,0,.25)}
.tag{top:196px;background:rgba(0,0,0,.75);font-family:var(--display);font-size:15px;padding:6px 18px}

/* footer */
.footer{top:3512px;left:0;width:1200px;height:491px;background:#0f0f0f}
.footer-brand{left:104px;top:160px;width:330px}
.footer-brand .mark{width:120px;height:120px;background:#4a4a4a;margin:0 0 20px 92px}
.footer-brand .name{font-family:var(--display);font-size:40px;color:#8a8a8a;letter-spacing:1px}
.col h3{font-family:var(--display);font-size:19px;font-weight:400;margin-bottom:12px}
.links{left:511px;top:180px}
.links li{list-style:none;font-size:15px;line-height:32px;margin-left:4px}
.contact{left:751px;top:180px}
.contact .row{display:flex;align-items:center;gap:14px;font-size:14.5px;line-height:21px;margin-bottom:20px}
.contact .ic{width:42px;height:42px;border-radius:50%;background:#bdbdbd;flex:none;display:flex;align-items:center;justify-content:center}
.rule{left:104px;top:437px;width:992px;height:1px;background:#333}
.copyright{top:450px;left:0;width:1200px;text-align:center;font-size:13.5px;color:var(--soft)}
</style>
</head>
<body>
<div class="page">

  <section class="hero abs" role="img" aria-label="Photo of roofers installing shingles on a roof">
    <div class="hero-copy abs">
      <div class="eyebrow display">Welcome to</div>
      <h1 class="display">Stonehaven<br>Construction</h1>
      <p>Stonehaven Construction is your source for roofing and siding in Minnesota.</p>
      <span class="btn">Get Started</span>
    </div>
    <div class="dots abs"><span></span><span></span><span></span></div>
  </section>

  <section class="services abs">
    <h2 class="section-title display abs" style="top:100px">What we do</h2>
    <div class="slider-arrow abs" style="left:34px">&#8592;</div>
    <div class="card abs" style="left:104px"><div class="photo" role="img" aria-label="Photo of roofers at work" style="background:linear-gradient(180deg,#3f5f86,#6a5a3e)">Roofing<span class="arrow">&#10140;</span></div></div>
    <div class="card abs" style="left:446px"><div class="photo" role="img" aria-label="Photo of grey vinyl siding" style="background:linear-gradient(135deg,#4a5060,#2e3340)">Siding<span class="arrow">&#10140;</span></div></div>
    <div class="card abs" style="left:788px"><div class="photo" role="img" aria-label="Photo of a white gutter on a house" style="background:linear-gradient(180deg,#3a4a32,#c9c9c9)">Gutters<span class="arrow">&#10140;</span></div></div>
    <div class="slider-arrow abs" style="left:1142px">&#8594;</div>
  </section>

  <svg class="abs" style="top:560px;left:0" width="1200" height="290" viewBox="0 0 1200 290" aria-hidden="true">
    <defs><linearGradient id="band" x1="0" y1="0" x2="0" y2="1"><stop offset="0" stop-color="#2f2f2f"/><stop offset="1" stop-color="#424242"/></linearGradient></defs>
    <polygon points="0,7 600,230 1200,7 1200,290 0,290" fill="url(#band)"/>
    <polygon points="62,35 600,190 1150,38 600,215" fill="#050505"/>
    <circle cx="600" cy="215" r="34" fill="#6a6a6a"/>
    <circle cx="600" cy="215" r="22" fill="none" stroke="#3a3a3a" stroke-width="5"/>
  </svg>

  <div class="topbar abs">
    <span class="mail abs">&#9993; | info@stonehavenbuild.example</span>
    <span class="phone abs">&#9742; | +1 555 010 2040</span>
    <div class="social abs"><span></span><span></span><span></span></div>
  </div>
  <nav class="navbar abs">
    <a style="left:104px">Roofing<span class="caret">&#8964;</span></a>
    <a style="left:208px">Siding<span class="caret">&#8964;</span></a>
    <a style="left:298px">Gutters<span class="caret">&#8964;</span></a>
    <a style="left:401px">Windows<span class="caret">&#8964;</span></a>
    <a style="left:733px">Repair<span class="caret">&#8964;</span></a>
    <a style="left:820px">Storm damage repair<span class="caret">&#8964;</span></a>
    <a style="left:1025px">Contact Us</a>
  </nav>
  <div class="brand abs"><div class="mark"></div><div class="name">STONEHAVEN</div></div>

  <section class="about abs">
    <div class="frame abs"></div>
    <div class="city abs" role="img" aria-label="Photo of a city skyline at dusk beside a stone bridge"></div>
    <div class="worker abs" role="img" aria-label="Photo of a roofer nailing shingles"></div>
    <div class="about-copy abs">
      <h2 class="display">About us</h2>
      <p>In 2016 Dale Hartley started helping people with their home improvement projects. His very first job was installing window trim for a wonderful homeowner in Forest lake MN.He did his best work and made sure he treated his first customer like family. Afterall, his first customer was Marion Hartley, his Mom.</p>
      <p>Today, Dale and the Stonehaven Construction team are helping homeowners around Minnesota; carrying the spirit of his first job onto every job they touch.</p>
      <span class="btn">Read more</span>
    </div>
  </section>

  <section class="promise abs" role="img" aria-label="Dim background photo of a crew working on a house">
    <h2 class="section-title display abs" style="top:96px">The Stonehaven promise</h2>
    <div class="avatar abs" role="img" aria-label="Portrait of the owner"></div>
    <p class="abs">You deserve timely service, high quality materials, expert installation, and a solid warranty. That is what we promise to deliver. I invite you to put us to the test today.</p>
    <div class="sign abs">
      <div class="sincerely">Sincerely,</div>
      <div class="who">Dale Hartley, Owner<br>Stonehaven Construction</div>
    </div>
  </section>

  <section class="work abs">
    <h2 class="section-title display abs" style="top:70px">See our work</h2>
    <p class="intro abs">Lorem ipsum dolor sit amet, consectetur adipiscing elit, sed do eiusmod tempor incididunt ut labore et dolore magna aliqua. Quis ipsum suspendisse ultrices gravida.</p>
    <div class="tabs abs"><span class="on">Roofing</span><span>Siding</span><span>Gutters</span><span>Windows</span><span>Repair</span><span>Storm damage repair</span></div>
    <div class="compare abs">
      <div class="before abs" role="img" aria-label="Photo of a house roof before replacement"></div>
      <div class="after abs" role="img" aria-label="Photo of the same house roof after replacement"></div>
      <div class="divider abs"></div>
      <div class="handle abs"></div>
      <div class="tag abs" style="left:26px">Before</div>
      <div class="tag abs" style="right:26px">After</div>
    </div>
  </section>

  <footer class="footer abs">
    <svg class="abs" style="top:0;left:0" width="1200" height="160" viewBox="0 0 1200 160" aria-hidden="true">
      <rect width="1200" height="160" fill="#000"/>
      <polygon points="0,0 1200,0 1200,170 600,20 0,170" fill="#000"/>
      <polygon points="0,170 600,6 1200,170" fill="#111"/>
      <polygon points="100,110 600,0 1130,118 600,30" fill="#3a3a3a"/>
    </svg>
    <div class="footer-brand abs"><div class="mark"></div><div class="name">STONEHAVEN</div></div>
    <div class="col links abs">
      <h3>Quick links</h3>
      <ul><li>Roofing</li><li>Siding</li><li>Gutters</li><li>Windows</li><li>Repair</li><li>Storm damage repair</li></ul>
    </div>
    <div class="col contact abs">
      <h3>Contact us</h3>
      <div class="row"><span class="ic"><svg width="16" height="20" viewBox="0 0 16 20"><path d="M8 0C3.6 0 0 3.4 0 7.7 0 13 8 20 8 20s8-7 8-12.3C16 3.4 12.4 0 8 0zm0 11a3 3 0 1 1 0-6 3 3 0 0 1 0 6z" fill="#333"/></svg></span><span>25, Stonehaven Yard<br>Lorem ipsum dolor sit amet850</span></div>
      <div class="row"><span class="ic"><svg width="18" height="18" viewBox="0 0 24 24"><path d="M6.6 10.8a15 15 0 0 0 6.6 6.6l2.2-2.2c.3-.3.7-.4 1-.2 1.1.4 2.3.6 3.6.6.6 0 1 .4 1 1V20c0 .6-.4 1-1 1C10.6 21 3 13.4 3 4c0-.6.4-1 1-1h3.5c.6 0 1 .4 1 1 0 1.3.2 2.5.6 3.6.1.3 0 .7-.2 1z" fill="#333"/></svg></span><span>+1 555 010 2040</span></div>
      <div class="row"><span class="ic"><svg width="18" height="14" viewBox="0 0 18 14"><rect width="18" height="14" rx="2" fill="#333"/><path d="M1 2l8 6 8-6" stroke="#bdbdbd" stroke-width="1.5" fill="none"/></svg></span><span>info@stonehavenbuild.example</span></div>
    </div>
    <div class="rule abs"></div>
    <div class="copyright abs">© Copyright 2024 Stonehaven Construction | All Rights Reserved</div>
  </footer>

</div>
</body>
</html>
```